Two Wine Labels, One Red One White

We are looking to create a brand image for our wines. There are two requirements by law that we need, however beyond that, the creativity comes from the designer. Required are:
On The Red Label, Alcohol 14.1White Label Alcohol 12.5, The Size, 750ML
SO One label for the red wine with alcohol at 14.1 in a 750 ML Bottle, and one Label for white with alcohol at 12.5 in a 750 ML bottle.

Hi All:
I have some more clarity to assist in the design work.
The Brand Name of the wine is Valquine for both the red and the white
The name should appear as Valquine with the Brackets around phonetical as seen here
[val-keen] Both the word and the phonetical spelling should appear.
and can be seen on lexiquarry.com The Brand Name text can be black
Label should be very light grey, I am trying to capture a Stone grey or texture from stone, although, NOT Marble.
The Red Label, The word "Red" should be in red
The White Label, The word "White" should be in White, all the original remaining elements remain as originally posted.

I look forward to hearing from you for any additional questions.
Updates

Just added a logo Not really seeing what we are trying to achieve, maybe using the logo in the design may assist

Target Market(s)

Wine Aficionados

Requirements
Must have
• Details described in Project Description above, these are required by law. The Name of the Brand will be posted shortly. For the moment if you take the project, just place red on one label and white on the other.
Nice to have
• These two wines are from California (USA), so the Sierra Nevada Mountains could be an inspiration, to outline of California or coast line, a vineyard (of course), a vine...We are in silicon valley, so there is a map of silicon valley with the Bay and ocean, something from a map could work, or let your creativity flow and not use any of these concepts.
Should not have
• I do not not care for decorative fonts, however all else is open

```html
<!DOCTYPE html>
<html lang="en">
<head>
<meta charset="utf-8">
<title>Valquine Red and White Labels</title>
<link rel="stylesheet" href="https://fonts.googleapis.com/css2?family=PT+Sans&family=Tinos&display=swap">
<style>
  :root {
    --page-bg: #f2f2f2;
    --stone-light: #e6e4e0;
    --stone-mid: #d8d5d0;
    --stone-edge: #cfcbc5;
    --ink-dark: #1a1616;
    --ink-light: #ffffff;
    --red-accent: #ec1c24;
    --white-accent: #d7e31e;
    --phonetic-white: #9aa40e;
    --sky: #3fa9dc;
    --ridge: #c4643c;
    --shore: #d59a4a;
    --water: #2c6cb4;
  }
  html, body {
    margin: 0;
    padding: 0;
    width: 1200px;
    height: 900px;
    overflow: hidden;
    background: var(--page-bg);
  }
  .canvas {
    position: relative;
    width: 1200px;
    height: 900px;
  }
  .label {
    position: absolute;
    top: 142px;
    width: 380px;
    height: 616px;
    background:
      radial-gradient(ellipse at 30% 20%, var(--stone-light) 0%, transparent 60%),
      radial-gradient(ellipse at 75% 80%, var(--stone-edge) 0%, transparent 65%),
      linear-gradient(160deg, var(--stone-light) 0%, var(--stone-mid) 100%);
    box-shadow: 0 10px 30px rgba(0,0,0,0.14);
  }
  .label--red { left: 190px; }
  .label--white { left: 630px; }
  .label__artwork {
    position: absolute;
    left: 0;
    top: 67px;
    width: 100%;
    height: 185px;
    background: linear-gradient(180deg,
      var(--sky) 0%,
      var(--ridge) 38%,
      var(--shore) 58%,
      var(--water) 78%,
      var(--sky) 100%);
  }
  .label__brand {
    position: absolute;
    top: 270px;
    width: 100%;
    margin: 0;
    text-align: center;
    color: var(--ink-dark);
    font-family: "PT Sans", sans-serif;
    font-weight: 400;
    font-size: 54px;
    line-height: 1;
  }
  .label__phonetic {
    position: absolute;
    top: 334px;
    width: 100%;
    margin: 0;
    text-align: center;
    font-family: "PT Sans", sans-serif;
    font-weight: 400;
    font-size: 23px;
    line-height: 1;
  }
  .label--red .label__phonetic { color: var(--red-accent); }
  .label--white .label__phonetic { color: var(--phonetic-white); }
  .label__variety {
    position: absolute;
    top: 374px;
    left: 0;
    width: 100%;
    height: 60px;
    margin: 0;
    display: flex;
    align-items: center;
    justify-content: center;
    box-sizing: border-box;
    color: var(--ink-light);
    font-family: "PT Sans", sans-serif;
    font-weight: 400;
    font-size: 60px;
    line-height: 1;
  }
  .label--red .label__variety {
    background: var(--red-accent);
    letter-spacing: 0.55em;
    padding-left: 0.55em;
  }
  .label--white .label__variety {
    background: var(--white-accent);
    letter-spacing: 0.62em;
    padding-left: 0.62em;
  }
  .label__facts {
    position: absolute;
    top: 474px;
    width: 100%;
    margin: 0;
    text-align: center;
    color: var(--ink-dark);
    font-family: "Tinos", serif;
    font-weight: 400;
    font-size: 20px;
    line-height: 34px;
  }
</style>
</head>
<body>
<main class="canvas">
  <section class="label label--red">
    <div class="label__artwork" role="img" aria-label="Painted landscape of blue sky, red-orange mountains and a blue lake"></div>
    <h1 class="label__brand">Valquine</h1>
    <p class="label__phonetic">[val-keen]</p>
    <p class="label__variety">RED</p>
    <p class="label__facts">Alcohol 14.1<br>750мл.</p>
  </section>
  <section class="label label--white">
    <div class="label__artwork" role="img" aria-label="Painted landscape of blue sky, red-orange mountains and a blue lake"></div>
    <h1 class="label__brand">Valquine</h1>
    <p class="label__phonetic">[val-keen]</p>
    <p class="label__variety">WHITE</p>
    <p class="label__facts">Alcohol 12.5<br>750мл.</p>
  </section>
</main>
</body>
</html>
```